Business Performance Improvement Book Cover Design Project

We need a book cover design for a new company, based in Eastern Australia, called Brovanta Consulting. We advise clients on process improvement, continuous improvement and business performance improvement, especially in the manufacturing areas and Fast Moving Consumer Goods industries.
We have a written a book designed to demonstrate our very high calibre of knowledge and to use as a marketing tool for prospective clients. We hope to give it out at training seminars and as a comprehensive business card.

Title of the book is: A rounded method for Enterprise Results Advancement.
Subtitle: Shape a Steady Refinement method to fit your firm's character.
Author: by Gareth Polwyn
Back Cover: No need for a bar code in this edition. An important aspect is that we will distribute by hand. Text below for back page.

'For the experienced Business Performers, this book is designed to offer an insight into the advantages and an example of an approach to Business Improvement. It is not the only way but it is tried and tested in world class companies and it works. For those new to Continuous Improvement, it offers a helpful introduction to a holistic business improvement system, an overview of important success factors and pitfalls, recommendations on how to implement tools and methods and a quick guide to see when to use which tools. '

'Consultancies are one of many tools management teams can engage and management must make sure the consultants tailor their approach to suit its business needs and culture and not vice versa.'

End of text for back cover.

Business Performance Improvement is also known as or can include:
Continuous Improvement
Process Improvement
Lean Six Sigma
Operational Excellence
Total Productive Maintenance
Varmeco Output Method
Total Quality Management
Business Process Re engineering
Yield Compass
=
Brovanta Consulting

The book size is 175 x 240 mm and will need a 10-15mm bleed. The spine is not known at this stage exactly and will need to be updated once the printing is finished but I suggest a 10mm until I have the exact size.

Our company colours are Pantone 288, R0,G75,B141, C100,M79,Y17,K3. Attached are some other publications that give a sense of what we like to portray, Some words which might add to this are: professional, elegance, quality, sleek.
Updates

Reason: After receiving the designs, I realised that I needed to update the brief with more and better quality information for designers to work with.

Target Market(s)

people in the accounting and insolvency industries, production managers and CEOs, Chief Operating Officers, members of the executive team of large companies and GMs of small companies.

Industry/Entity Type

Marketing

Requirements
Must have
• Communicate an image that shows an improvement or increase of something.
Very professional and elegant
Emphasis on the words 'Business Performance Improvement' in the title, subtitle also important
Must appeal to a high-end of the market audience
Nice to have
• Recommendation for your cover to be gloss or matt in print
Image can be indirectly related to money but not specifically
Somehow that it matches or is not so different to the attached brochure
Should not have
• Not be too loud or commercial
Book jacket. WIll be printed as soft cover first run and hard cover 2nd run

```html
<!DOCTYPE html>
<html lang="en">
<head>
<meta charset="utf-8">
<title>A Rounded Method for Enterprise Results Advancement — Book Cover</title>
<link rel="stylesheet" href="https://fonts.googleapis.com/css2?family=Comfortaa:wght@500;700&display=swap">
<style>
  :root {
    --cover-blue: #124b8b;
    --paper-white: #ffffff;
    --ornament-light: rgba(214, 222, 240, 0.55);
    --ornament-fade: rgba(150, 170, 215, 0.15);
  }
  html, body {
    margin: 0;
    padding: 0;
    overflow: hidden;
    background: var(--cover-blue);
  }
  .cover {
    position: relative;
    width: 846px;
    height: 1200px;
    background: var(--cover-blue);
    overflow: hidden;
    font-family: "Comfortaa", sans-serif;
    color: var(--paper-white);
  }
  .cover-shapes {
    position: absolute;
    inset: 0;
  }
  .ornament {
    position: absolute;
    border-radius: 45%;
  }
  .ornament--top-left {
    left: 28px;
    top: 18px;
    width: 275px;
    height: 275px;
    background: radial-gradient(circle at 40% 45%, var(--ornament-light), var(--ornament-fade) 70%, transparent 80%);
  }
  .ornament--bottom-right {
    left: 535px;
    top: 905px;
    width: 330px;
    height: 320px;
    background: radial-gradient(circle at 55% 55%, var(--ornament-light), var(--ornament-fade) 70%, transparent 80%);
  }
  .book-title {
    position: absolute;
    right: 44px;
    top: 62px;
    margin: 0;
    text-align: right;
    font-weight: 700;
    font-size: 60px;
    line-height: 108px;
    letter-spacing: 0.5px;
  }
  .book-title span { display: block; }
  .book-subtitle {
    position: absolute;
    right: 46px;
    top: 596px;
    margin: 0;
    text-align: right;
    font-weight: 700;
    font-size: 28px;
    line-height: 55px;
  }
  .book-subtitle span { display: block; }
  .book-author {
    position: absolute;
    left: 42px;
    top: 1122px;
    margin: 0;
    font-weight: 700;
    font-size: 26px;
    letter-spacing: 0.3px;
  }
</style>
</head>
<body>
<main class="cover">
  <svg class="cover-shapes" width="846" height="1200" viewBox="0 0 846 1200" aria-hidden="true">
    <polygon class="side-wedge" points="0,150 218,452 218,740 0,1022" fill="var(--paper-white)"/>
    <g class="rising-bars" fill="var(--paper-white)">
      <rect x="236" y="478" width="14" height="232"/>
      <rect x="254" y="496" width="13" height="196"/>
      <rect x="271" y="515" width="13" height="158"/>
      <polygon points="300,574 320,595 300,616"/>
    </g>
  </svg>

  <div class="ornament ornament--top-left" role="img" aria-label="Flowing floral swirl ornament in pale blue and white"></div>
  <div class="ornament ornament--bottom-right" role="img" aria-label="Stylised growing tree with floral swirls in pale blue and white"></div>

  <h1 class="book-title">
    <span>A Rounded</span>
    <span>Method For</span>
    <span>Enterprise</span>
    <span>Results</span>
    <span>Advancement</span>
  </h1>

  <p class="book-subtitle">
    <span>Shape a</span>
    <span>Steady Refinement</span>
    <span>method to fit your</span>
    <span>firm's character.</span>
  </p>

  <p class="book-author">Gareth Polwyn B. Mech Eng., M. Sc (HVZ)</p>
</main>
</body>
</html>
```